Varnor Immigration _Cloud-based, boutique law firm serving clients worldwide in US Immigration Law

I need a website for my new US immigration law firm that will be based in Montreal, QC Canada but serve clients worldwide to achieve their US immigration goals. This will be a boutique firm offering attentive and compassionate service to our corporate and individual clients. I'd like the site to be fresh, modern, sophisticated and easy to read.

I will need a home page, about/bio page, services page, and contact me page with a form so potential clients could email inquiries and also schedule consultations. I would also like a 'Book a Consultation' button on the home page (easily visible).

The longest website page is going to be the 'Services' tab, which I'd like to break down to services for Employers and services Individuals, with further sub-sets of services to each type of client. I envision images with short text that display longer text when hoovering over.

To start, I would have 3 subsets of services for Employers and 5 subsets of services for Individuals. I will need the ability to expand/edit these pages in Wix interface as we grow.

The site will need to be in English and in French.

I like the color blue and the final design should communicate the firm's core values: integrity and compassion. In other words, we do right, no matter what and are understanding to individual circumstances. I'd like the site to convey sophistication and accessibility. I don't like staged stock photos of people. Sites with a lot of stock photos of people feels unauthentic to me.

Logo draft is attached in jpeg. Navy and gold colors.
Example of 4 law firm sites I like below:
- https://www.quilbanelaw.example/
-https://www.zetrivlaw.example/
-https://harlowinappeals.example/
-https://www.ombrekilaw.example/

Target Market(s)

Small-medium sized businesses (10-999 employees) in US with foreign workforce; Foreign entrepreneurs wishing to implant in the US

Industry/Entity Type

Law

Coding

Font styles to use
Sans Serif

Colors

Designer to choose colors to be used in the design.

Requirements
Must have
• Great Home Page (Grabs attention with eye-catching images/text; Immediately establishes credibility; Provides an overview of services; Encourages visitor to take the next action.)
Nice to have
• Images of Montreal (where firm is based); Images of bridges (symbolizes progress, movement, connections)
Should not have
• Non-authentic photos: staged people at desks or pictures of court buildings.

```html
<!DOCTYPE html>
<html lang="en">
<head>
<meta charset="utf-8">
<title>Varnor Immigration</title>
<link rel="stylesheet" href="https://fonts.googleapis.com/css2?family=Libre+Baskerville:wght@400;700&family=Jost:wght@400;500&display=swap">
<style>
:root{
  --navy:#2e3352;
  --gold:#857849;
  --gold-light:#a99a5f;
  --royal:#0d1190;
  --white:#ffffff;
  --ink:#3a3a3a;
  --lav:#e6e5f3;
  --sky:#6cb8e8;
}
*{margin:0;padding:0;box-sizing:border-box}
html,body{width:1200px;height:2800px;overflow:hidden}
body{position:relative;font-family:'Jost',sans-serif;color:var(--ink);background:var(--white)}
.abs{position:absolute}
.serif{font-family:'Libre Baskerville',serif}

/* header */
.header{left:0;top:0;width:1200px;height:115px;background:var(--navy)}
.topbar{left:378px;top:0;width:710px;height:39px;background:var(--gold);clip-path:polygon(0 0,100% 0,100% 100%,40px 100%)}
.topbar .item{position:absolute;top:11px;color:#fff;font-size:12px;display:flex;align-items:center;gap:8px}
.lang{left:970px;top:0;width:118px;height:39px;background:#3f4160;color:#fff;font-size:12px;display:flex;align-items:center;justify-content:center;gap:8px}
.brand{left:50px;top:20px;display:flex;align-items:center;gap:14px}
.brand-dot{width:74px;height:74px;border-radius:50%;background:var(--gold);opacity:.85}
.brand-name{font-family:'Libre Baskerville',serif;color:var(--gold-light);font-size:23px;letter-spacing:4px;line-height:31px}
.brand-sub{font-family:'Libre Baskerville',serif;color:var(--gold-light);font-size:10px;letter-spacing:3px;margin-top:4px}
.nav{top:74px;left:498px;display:flex;gap:46px;color:#fff;font-size:15px}
.nav .active{color:var(--gold-light)}
.callout{left:926px;top:52px;display:flex;align-items:center;gap:12px}
.callout .ring{width:48px;height:48px;border:2px solid var(--gold);border-radius:50%;display:flex;align-items:center;justify-content:center}
.callout .t1{font-family:'Libre Baskerville',serif;font-style:italic;color:#fff;font-size:14px}
.callout .t2{color:var(--gold-light);font-size:22px;font-weight:500}

/* hero */
.hero{left:0;top:115px;width:1200px;height:588px;background:linear-gradient(180deg,#5db3ec 0%,#9fd3f3 55%,#c9d8e0 100%)}
.hero-title{left:107px;top:305px;font-family:'Libre Baskerville',serif;font-weight:700;font-size:50px;color:#1c1c2c;letter-spacing:1px}
.btn{display:flex;align-items:center;height:48px;color:#fff;font-family:'Libre Baskerville',serif;font-size:13px}
.btn .cap{width:50px;height:100%;background:var(--royal);display:flex;align-items:center;justify-content:center;clip-path:polygon(0 0,100% 0,80% 100%,0 100%)}
.btn .cap i{width:28px;height:28px;border-radius:50%;background:var(--gold-light);display:block}
.btn .body{height:100%;background:var(--gold);display:flex;align-items:center;gap:12px;padding:0 14px 0 8px;margin-left:-10px}
.dots{left:574px;top:650px;display:flex;gap:10px}
.dots i{width:11px;height:11px;border-radius:50%;background:#a8a08a;display:block}
.dots i.on{background:var(--gold)}

/* about */
.about-band{left:0;top:703px;width:550px;height:600px;background:var(--gold)}
.about-watermark{left:572px;top:1190px;font-family:'Jost',sans-serif;font-weight:500;font-size:108px;color:#f3f3f3}
.about-card{left:214px;top:785px;width:772px;height:434px;background:#fff;border-radius:8px;box-shadow:0 6px 24px rgba(0,0,0,.12);overflow:hidden}
.about-photo{left:0;top:0;width:391px;height:434px;background:linear-gradient(160deg,#e4e4e4,#cfd0d0)}
.about-thumb{left:345px;top:324px;width:90px;height:90px;background:linear-gradient(160deg,#d8d2cc,#bdb5ae);border:3px solid #fff}
.about-h{left:490px;top:35px;width:260px;text-align:center;font-family:'Libre Baskerville',serif;font-weight:700;font-size:34px;color:var(--gold)}
.rule{height:2px;background:var(--royal)}
.about-p{left:438px;top:91px;width:281px;font-size:15px;line-height:25px;text-align:justify;text-align-last:center}

/* services */
.services{left:0;top:1303px;width:1200px;height:607px;background:linear-gradient(180deg,#0c1094 0%,#1d2a8f 60%,#15248a 100%)}
.services-h{left:0;top:1383px;width:1200px;text-align:center;font-family:'Libre Baskerville',serif;font-weight:700;font-size:34px;color:#fff}
.svc{top:1469px;width:391px;height:354px;background:#fff;border-radius:6px;text-align:center}
.svc h3{position:absolute;left:0;top:146px;width:100%;font-family:'Libre Baskerville',serif;font-size:22px;color:var(--gold)}
.svc p{position:absolute;left:17px;top:185px;width:357px;font-size:15px;line-height:25px}
.svc .more{position:absolute;left:0;top:317px;width:100%;font-family:'Libre Baskerville',serif;font-size:12px;color:var(--gold)}
.svc svg{position:absolute;left:154px;top:30px}

/* map & form */
.map{left:0;top:1910px;width:1200px;height:520px;background:linear-gradient(135deg,#eef0ec 0%,#e4e9e1 50%,#eceef0 100%)}
.pin-card{left:266px;top:2130px;width:200px;height:70px;background:#fff;border-radius:4px;box-shadow:0 2px 8px rgba(0,0,0,.2);font-size:13px;line-height:20px;padding:6px 0 0 84px}
.pin-card i{position:absolute;left:6px;top:6px;width:72px;height:58px;background:linear-gradient(160deg,#7aa9d6,#8d8a80);display:block}
.form{left:568px;top:1990px;width:520px;height:355px;background:var(--gold);border-radius:6px}
.field{position:absolute;background:#fff;border-radius:22px;font-family:'Libre Baskerville',serif;font-size:12px;color:#333;padding:16px 0 0 19px}

/* contact strip */
.strip{left:0;top:2430px;width:1200px;height:122px;background:var(--lav)}
.ci{top:2467px;height:50px;background:#fff;display:flex;align-items:center;font-size:14px;line-height:20px}
.ci .ico{width:52px;height:50px;background:var(--gold);display:flex;align-items:center;justify-content:center;margin-right:10px;flex:none}

/* footer */
.footer{left:0;top:2552px;width:1200px;height:155px;background:var(--navy)}
.fnav{left:587px;top:2619px;display:flex;gap:52px;color:#fff;font-size:17px}
.copy{left:0;top:2745px;width:1200px;text-align:center;font-size:15px;color:#333}
</style>
</head>
<body>

<header>
  <div class="abs header"></div>
  <div class="abs topbar">
    <div class="item" style="left:56px"><span style="width:14px;height:14px;background:#fff;display:inline-block"></span>Connect with Elise Varnor</div>
    <div class="item" style="left:212px;top:6px;width:1px;height:26px;background:rgba(255,255,255,.5)"></div>
    <div class="item" style="left:262px">
      <svg width="16" height="12" viewBox="0 0 16 12"><rect x="0.5" y="0.5" width="15" height="11" rx="1" fill="#fff"/><path d="M1 1l7 6 7-6" stroke="#857849" fill="none"/></svg>
      varnorimmigration@mail.example</div>
  </div>
  <div class="abs lang">
    <svg width="18" height="18" viewBox="0 0 18 18" fill="none" stroke="#fff" stroke-width="1.2"><circle cx="9" cy="9" r="8"/><ellipse cx="9" cy="9" rx="3.5" ry="8"/><path d="M1 9h16M2.5 5h13M2.5 13h13"/></svg>
    English <span style="font-size:9px">▼</span></div>

  <div class="abs brand">
    <div class="brand-dot"></div>
    <div>
      <div class="brand-name">VARNOR<br>IMMIGRATION</div>
      <div class="brand-sub">ELISE VARNOR, ATTORNEY</div>
    </div>
  </div>

  <nav class="abs nav">
    <span class="active">Home</span><span>Our Services</span><span>About Us</span><span>Contact Us</span>
  </nav>

  <div class="abs callout">
    <div class="ring"><svg width="22" height="22" viewBox="0 0 24 24" fill="none" stroke="#857849" stroke-width="1.6"><path d="M5 3h4l2 5-3 2a11 11 0 0 0 6 6l2-3 5 2v4a2 2 0 0 1-2 2A17 17 0 0 1 3 5a2 2 0 0 1 2-2z"/></svg></div>
    <div><div class="t1">Get Your Free Appointment</div><div class="t2">+1 (555) 014 2290</div></div>
  </div>
</header>

<section>
  <div class="abs hero" role="img" aria-label="Photograph of a green steel truss bridge spanning into Montreal under a blue sky"></div>
  <h1 class="abs hero-title">VARNOR IMMIGRATION</h1>
  <div class="abs btn" style="left:111px;top:389px">
    <span class="cap"><i></i></span>
    <span class="body">BOOK A CONSULTATION <span>→</span></span>
  </div>
  <div class="abs dots"><i></i><i class="on"></i><i></i></div>
</section>

<section>
  <div class="abs about-band" role="img" aria-label="Soft gold-tinted portrait backdrop"></div>
  <div class="abs about-watermark">Elise Varnor</div>
  <div class="abs about-card">
    <div class="abs about-photo" role="img" aria-label="Portrait photograph of the attorney in a blue blouse"></div>
    <div class="abs about-thumb" role="img" aria-label="Small headshot of the attorney"></div>
    <h2 class="abs about-h">ABOUT US</h2>
    <div class="abs rule" style="left:552px;top:78px;width:55px"></div>
    <p class="abs about-p">Saerspiciatis undeasepoiise omnis iste natus error sasdjk asdoaasfit voluptatem accusan tium doloremque laudantium, tsadotam rem aperiam, ease aqusehutje ipaefdsa quae ab illo inventore veritatis edfsgdfsase quasi architecto beatae vitae dicasdfeta sunt explicabo. Nemo enim ipsam voluasptatem quia volupta sde sessitasese aspernatur autodit aut fugitsdsed quia consequuntur magni dolores eos qui.</p>
    <div class="abs btn" style="left:486px;top:357px">
      <span class="cap"><i></i></span>
      <span class="body">LEARN MORE &nbsp;&nbsp;&nbsp;<span>→</span></span>
    </div>
  </div>
</section>

<section>
  <div class="abs services" role="img" aria-label="Deep blue tinted Montreal skyline at dusk"></div>
  <h2 class="abs services-h">OUR SERVICES</h2>
  <div class="abs rule" style="left:574px;top:1429px;width:54px;background:#fff"></div>

  <div class="abs svc" style="left:167px">
    <svg width="84" height="84" viewBox="0 0 84 84" fill="none" stroke="#222" stroke-width="2"><rect x="18" y="4" width="62" height="76" rx="4"/><path d="M50 20h22M50 32h22M50 44h22M50 56h22"/><circle cx="26" cy="44" r="17" stroke="#857849"/><circle cx="26" cy="40" r="6"/><path d="M16 54c3-6 17-6 20 0M38 56l14 14"/></svg>
    <h3>EMPLOYERS</h3>
    <p>Saerspiciatis undeasepoiise omasdnis iste natus error sasdjk asdoaasfit voluasdkl sloseptatem accusan tium doloremque laudantium, tsadotam rem aperiam, ease aqusehutje ipaefdsa quae aassb illo inventore veritatis edfsgdfsase quasi architecto beatae vitae.</p>
    <div class="more">LEARN MORE →</div>
  </div>

  <div class="abs svc" style="left:642px">
    <svg width="84" height="84" viewBox="0 0 84 84" fill="none" stroke="#222" stroke-width="2"><path d="M42 3l36 20v38L42 81 6 61V23z"/><circle cx="42" cy="30" r="11"/><path d="M20 64c2-14 12-18 22-18s20 4 22 18"/><path d="M42 54l9 5v10l-9 5-9-5V59z" stroke="#222"/><circle cx="42" cy="64" r="3"/></svg>
    <h3>INDIVIDUALS</h3>
    <p>Saerspiciatis undeasepoiise omasdnis iste natus error sasdjk asdoaasfit voluasdkl sloseptatem accusan tium doloremque laudantium, tsadotam rem aperiam, ease aqusehutje ipaefdsa quae aassb illo inventore veritatis edfsgdfsase quasi architecto beatae vitae.</p>
    <div class="more">LEARN MORE →</div>
  </div>
</section>

<section>
  <div class="abs map" role="img" aria-label="Street map of the office surroundings"></div>
  <svg class="abs" style="left:238px;top:2162px" width="22" height="28" viewBox="0 0 22 28"><path d="M11 1C5 1 1 5 1 11c0 7 10 16 10 16s10-9 10-16C21 5 17 1 11 1z" fill="#e53935"/><circle cx="11" cy="11" r="4" fill="#fff"/></svg>
  <div class="abs pin-card"><i role="img" aria-label="Office building thumbnail"></i>212, Caldwren,<br>Ohio, USA<br>45019</div>

  <form class="abs form">
    <div class="field" style="left:21px;top:25px;width:233px;height:42px">Your Name</div>
    <div class="field" style="left:266px;top:25px;width:233px;height:42px">Last Name</div>
    <div class="field" style="left:21px;top:80px;width:478px;height:42px">Email</div>
    <div class="field" style="left:21px;top:136px;width:478px;height:122px">Enter Your Message</div>
    <div class="abs btn" style="left:184px;top:279px;height:48px">
      <span style="width:50px;height:48px;background:#fff;display:flex;align-items:center;justify-content:center"><i style="width:28px;height:28px;border-radius:50%;background:var(--gold-light);display:block"></i></span>
      <span style="height:48px;background:var(--royal);display:flex;align-items:center;gap:12px;padding:0 6px 0 22px;clip-path:polygon(10px 0,100% 0,100% 100%,0 100%);margin-left:-8px">SUBMIT <span>→</span></span>
    </div>
  </form>
</section>

<section>
  <div class="abs strip"></div>
  <div class="abs ci" style="left:200px;width:201px">
    <span class="ico"><svg width="18" height="24" viewBox="0 0 18 24"><path d="M9 1C4.5 1 1 4.5 1 9c0 6 8 14 8 14s8-8 8-14C17 4.5 13.5 1 9 1z" fill="#fff"/><circle cx="9" cy="9" r="3" fill="#857849"/></svg></span>
    <span>212, Caldwren, Ohio,<br>USA, 45019</span>
  </div>
  <div class="abs ci" style="left:500px;width:201px">
    <span class="ico"><svg width="22" height="22" viewBox="0 0 24 24" fill="none" stroke="#fff" stroke-width="1.8"><path d="M5 3h4l2 5-3 2a11 11 0 0 0 6 6l2-3 5 2v4a2 2 0 0 1-2 2A17 17 0 0 1 3 5a2 2 0 0 1 2-2z"/></svg></span>
    <span style="font-size:16px">+1 (555) 014 2290</span>
  </div>
  <div class="abs ci" style="left:799px;width:234px">
    <span class="ico"><svg width="20" height="15" viewBox="0 0 16 12"><rect x="0.5" y="0.5" width="15" height="11" rx="1" fill="#fff"/><path d="M1 1l7 6 7-6" stroke="#857849" fill="none"/></svg></span>
    <span style="font-size:13px">varnorimmigration@mail.example</span>
  </div>
</section>

<footer>
  <div class="abs footer"></div>
  <div class="abs brand" style="left:115px;top:2585px">
    <div class="brand-dot"></div>
    <div>
      <div class="brand-name">VARNOR<br>IMMIGRATION</div>
      <div class="brand-sub">ELISE VARNOR, ATTORNEY</div>
    </div>
  </div>
  <nav class="abs fnav"><span>Home</span><span>Our Services</span><span>About Us</span><span>Contact Us</span></nav>
  <p class="abs copy">©2023. All Rights Reserved.</p>
</footer>

</body>
</html>
```